Rice Cakes Packing Desing

We need a simple (4 color) yet colorful, atractive design for a Rice Cake polypropylene bag. We are expanding our line to include 8-10 different flavors with each bag being a different color for easy identificaction. We are starting right with the first design. We already have "sample model" (of an existing product in the usa market) upon which we believe that our design could be based on (as an idea of a simple 4 color plastic bag design), which we are including in this post. We are also including an image of Brindle Rice Cakes plastic bag that has a round front window that shows the product inside the bag, which we also would like to include in our design. We already have a brand name and a logo design. The bag's dimension is about 20cms (wide) 30cms (tall) and it will contain about 12 rice cakes inside. (I HAVE ATTACHED A COUPLE OF IMAGES OF A PRINTED POLYPROPYLENE RICE CAKES BAG FOR YOUR REFERENCE)
Updates

Project Deadline Extended
Reason: We want to provide the designers with NUTRITIONAL INFORMATION, Bar Code, Company information, Ingredients, important pointers, etc. to be incorporated into the design. We would like to provide a few more days in order to fully integrate the back & front text into the package design in order to attain a perfectly balanced and well presented package. So far we have received some very interesting and highly viable proposals and we would like to provide the designers the necessary text information in order to have a complete, fully designed, great-looking package. We feel that with the extension the final design can be completed and we can have an opportunity to review, incorporate/change/modify any details before choosing the final design. Great designs have been submitted and we will definitely choose one before the newly proposed deadline. Thanks to all!

Target Market(s)

Although the concept of RICE CAKES might very well have its origins in ASIA the idea is to create a design (logo & pack) that will convey a message to the end consumer that our brand name stands for "FRESHNESS", "HEALTHY", "NATURE'S BEST", "TOP GRAINS", "GOODNESS", in short if you consume are products "IT IS GOOD FOR YOU!" (not only for people who love oriental food). We would like to have a product image that says "Hey! This looks Healthy & Tasty" (non-fattening, yummy and good!)

When you buy a pack of GRANOLAS what do you think about? What do you believe it is that you are buying? Good, Healthy Stuff? Good Tasting? Good for you? That's the idea!

Besides Rice Cakes are super light, fluffy, crunchy and easy to digest that it makes it a great Snack for everyone! Kids & Adults!

We need the full complete design of the actual bag (where the Rice Cakes will be packed) in order to start production of the bags right.

Industry/Entity Type

Plastic

Requirements
Must have
• We already have a local company in Mexico City that makes printed polypropylene bags. They are only waiting for the bag design in order to print the 20cms x 30cms bags.
Kindly consider that on the back Nutritional Information will be needed as well as a BarCode, company information, some bullets (pointing to the most important benefits of the product), etc. We will provide all the text information.
Nice to have
• Kindly take a look at the newly uploaded images from "TORVE" Rice Cake packages. They are a good example of how to accomplish a great looking design using only 4 colors (which saves a lot in printing costs)
Should not have
• We do NOT want to have a design that says "This is ORIENTAL food". We don't want it to appear like "Sushi Rice" or "Japanese food", etc.

```html
<!DOCTYPE html>
<html lang="es">
<head>
<meta charset="utf-8">
<title>Granvela Rice Cakes – Regular Salted</title>
<link href="https://fonts.googleapis.com/css2?family=Oswald:wght@700&family=Pinyon+Script&family=Arimo:wght@700&display=swap" rel="stylesheet">
<style>
  :root{
    --page:#e9ecee;
    --bag-white:#ffffff;
    --blue:#1f8fd8;
    --blue-light:#8fd0f3;
    --blue-deep:#1669b8;
    --navy:#252a80;
    --gold:#e6b43a;
    --green:#4c6f3b;
    --green-light:#6d8f55;
    --orange:#f3a31b;
    --rice-light:#e6dcc6;
    --rice-dark:#b9a684;
    --cream:#f4f1df;
  }
  html,body{margin:0;padding:0;width:671px;height:1200px;overflow:hidden;background:var(--page);}
  .canvas{position:relative;width:671px;height:1200px;}
  .bag-front{position:absolute;left:105px;top:5px;width:460px;height:1190px;display:block;}
  .brand-name{font-family:"Arimo",sans-serif;font-weight:700;font-size:36px;fill:var(--navy);letter-spacing:4px;}
  .product-name{font-family:"Oswald",sans-serif;font-weight:700;font-size:66px;fill:var(--navy);}
  .flavour-name{font-family:"Pinyon Script",cursive;font-size:34px;fill:var(--cream);}
  .nutri-heading,.nutri-footnote{font-family:"Arimo",sans-serif;font-weight:700;font-size:12px;fill:var(--navy);}
  .nutri-label{font-family:"Arimo",sans-serif;font-weight:700;font-size:10.5px;fill:#1b1b3a;}
  .nutri-percent{font-family:"Arimo",sans-serif;font-weight:700;font-size:12px;fill:#ffffff;}
  .net-weight{font-family:"Arimo",sans-serif;font-weight:700;font-size:21px;fill:var(--navy);stroke:#ffffff;stroke-width:3px;paint-order:stroke;}
</style>
</head>
<body>
<div class="canvas">
  <svg class="bag-front" viewBox="0 0 460 1190" xmlns="http://www.w3.org/2000/svg">
    <defs>
      <linearGradient id="rice-fill" x1="0" y1="0" x2="0" y2="1">
        <stop offset="0" stop-color="var(--rice-light)"/>
        <stop offset="1" stop-color="var(--rice-dark)"/>
      </linearGradient>
      <linearGradient id="window-fade" x1="0" y1="0" x2="0" y2="1">
        <stop offset="0" stop-color="#ffffff" stop-opacity="1"/>
        <stop offset="1" stop-color="#ffffff" stop-opacity="0"/>
      </linearGradient>
      <linearGradient id="pattern-fill" x1="0" y1="0" x2="1" y2="1">
        <stop offset="0" stop-color="var(--blue-deep)"/>
        <stop offset="0.45" stop-color="var(--blue)"/>
        <stop offset="0.75" stop-color="var(--blue-light)"/>
        <stop offset="1" stop-color="var(--blue)"/>
      </linearGradient>
    </defs>

    <rect class="bag-body" x="0" y="0" width="460" height="1190" rx="22" fill="var(--bag-white)"/>

    <rect class="product-window" x="80" y="330" width="300" height="240" fill="url(#rice-fill)" role="img" aria-label="Stacked rice cakes seen through the bag window"/>
    <rect class="window-top-fade" x="80" y="325" width="300" height="40" fill="url(#window-fade)"/>

    <rect class="brand-mark" x="204" y="196" width="52" height="52" fill="var(--gold)"/>
    <text class="brand-name" x="230" y="302" text-anchor="middle">GRANVELA</text>

    <path class="pattern-field" d="M0 525 L85 445 L230 560 L375 445 L460 525 L460 1168 Q460 1190 438 1190 L22 1190 Q0 1190 0 1168 Z" fill="url(#pattern-fill)" role="img" aria-label="Blue diagonal plaid pattern"/>
    <polyline class="accent-line" points="0,517 85,437 100,449" fill="none" stroke="var(--orange)" stroke-width="6"/>
    <polyline class="accent-line" points="360,449 375,437 460,517" fill="none" stroke="var(--orange)" stroke-width="6"/>

    <path class="product-label" d="M230 560 L445 690 L445 790 L230 905 L15 790 L15 690 Z" fill="#ffffff"/>
    <ellipse class="grain-ornament" cx="215" cy="625" rx="40" ry="36" fill="var(--gold)" opacity="0.75" role="img" aria-label="Golden rice stalk ornament"/>
    <text class="product-name" x="230" y="735" text-anchor="middle">RICE CAKES</text>
    <path class="flavour-ribbon" d="M34 748 L426 748 L410 777 L426 806 L34 806 L50 777 Z" fill="var(--green)"/>
    <rect x="50" y="748" width="360" height="4" fill="var(--green-light)"/>
    <text class="flavour-name" x="230" y="789" text-anchor="middle">Regular Salted</text>

    <text class="nutri-heading" x="230" y="955" text-anchor="middle">Una porción aporta:</text>
    <g class="nutri-badge" transform="translate(104 964)">
      <rect width="58" height="80" rx="18" fill="#ffffff" stroke="var(--navy)" stroke-width="3"/>
      <path d="M1.5 54 H56.5 V62 Q56.5 78.5 40 78.5 H18 Q1.5 78.5 1.5 62 Z" fill="var(--navy)"/>
      <text class="nutri-label" x="29" y="26" text-anchor="middle">Energía</text>
      <text class="nutri-label" x="29" y="40" text-anchor="middle">35 Cal</text>
      <text class="nutri-percent" x="29" y="71" text-anchor="middle">2%</text>
    </g>
    <g class="nutri-badge" transform="translate(166 964)">
      <rect width="58" height="80" rx="18" fill="#ffffff" stroke="var(--navy)" stroke-width="3"/>
      <path d="M1.5 54 H56.5 V62 Q56.5 78.5 40 78.5 H18 Q1.5 78.5 1.5 62 Z" fill="var(--navy)"/>
      <text class="nutri-label" x="29" y="20" text-anchor="middle">Grasa</text>
      <text class="nutri-label" x="29" y="33" text-anchor="middle">Saturada</text>
      <text class="nutri-label" x="29" y="46" text-anchor="middle">0 g</text>
      <text class="nutri-percent" x="29" y="71" text-anchor="middle">0%</text>
    </g>
    <g class="nutri-badge" transform="translate(228 964)">
      <rect width="58" height="80" rx="18" fill="#ffffff" stroke="var(--navy)" stroke-width="3"/>
      <path d="M1.5 54 H56.5 V62 Q56.5 78.5 40 78.5 H18 Q1.5 78.5 1.5 62 Z" fill="var(--navy)"/>
      <text class="nutri-label" x="29" y="26" text-anchor="middle">Azúcares</text>
      <text class="nutri-label" x="29" y="40" text-anchor="middle">0 g</text>
      <text class="nutri-percent" x="29" y="71" text-anchor="middle">0%</text>
    </g>
    <g class="nutri-badge" transform="translate(290 964)">
      <rect width="58" height="80" rx="18" fill="#ffffff" stroke="var(--navy)" stroke-width="3"/>
      <path d="M1.5 54 H56.5 V62 Q56.5 78.5 40 78.5 H18 Q1.5 78.5 1.5 62 Z" fill="var(--navy)"/>
      <text class="nutri-label" x="29" y="26" text-anchor="middle">Sodio</text>
      <text class="nutri-label" x="29" y="40" text-anchor="middle">10 mg</text>
      <text class="nutri-percent" x="29" y="71" text-anchor="middle">0%</text>
    </g>
    <text class="nutri-footnote" x="230" y="1062" text-anchor="middle">% diario en una dieta de 2 000 Cal</text>

    <text class="net-weight" x="230" y="1106" text-anchor="middle">Net wt. / Contenido Neto</text>
    <text class="net-weight" x="230" y="1134" text-anchor="middle">4.0 oz / 120g</text>
  </svg>
</div>
</body>
</html>
```